The Plate Compass

Cutting Through the Noise to What Actually Works.

Nutrition book

Target Market(s)

People looking to be or get healthy and eat right.

```html
<!DOCTYPE html>
<html lang="en">
<head>
<meta charset="utf-8">
<title>The Plate Compass</title>
<link href="https://fonts.googleapis.com/css2?family=Inter:ital,wght@0,400;0,500;0,800;1,400;1,500&display=swap" rel="stylesheet">
<style>
  :root {
    --paper: #f9f9f9;
    --forest: #2b7f62;
    --ink: #1a1a18;
    --rule: #eef3ef;
    --muted: #5f5f5a;
  }
  * { margin: 0; padding: 0; box-sizing: border-box; }
  html, body { width: 811px; height: 1200px; overflow: hidden; background: var(--paper); }
  .cover {
    position: relative;
    width: 811px;
    height: 1200px;
    background: var(--paper);
    font-family: "Inter", Arial, sans-serif;
    color: var(--ink);
  }
  .cover__eyebrow {
    position: absolute;
    top: 66px;
    left: 0;
    width: 100%;
    text-align: center;
    font-size: 23px;
    font-weight: 400;
    letter-spacing: 0.01em;
    color: var(--forest);
  }
  .cover__title {
    position: absolute;
    top: 106px;
    left: 0;
    width: 100%;
    text-align: center;
    font-size: 75px;
    font-weight: 800;
    line-height: 86px;
    letter-spacing: -0.01em;
    text-transform: uppercase;
  }
  .cover__band {
    position: absolute;
    top: 296px;
    left: 0;
    width: 811px;
    height: 590px;
    background: var(--forest);
  }
  .cover__band svg { display: block; }
  .pyramid__label {
    font-family: "Inter", Arial, sans-serif;
    font-style: italic;
    font-weight: 400;
    fill: var(--ink);
    letter-spacing: -0.02em;
  }
  .cover__note {
    position: absolute;
    top: 911px;
    left: 0;
    width: 100%;
    text-align: center;
    font-size: 21px;
    font-style: italic;
    font-weight: 500;
    letter-spacing: -0.01em;
  }
  .cover__subtitle {
    position: absolute;
    top: 980px;
    left: 0;
    width: 100%;
    text-align: center;
    font-size: 21px;
    font-style: italic;
    line-height: 27px;
    color: var(--muted);
  }
  .cover__author {
    position: absolute;
    top: 1099px;
    left: 0;
    width: 100%;
    text-align: center;
    font-size: 24px;
    font-style: italic;
    font-weight: 500;
    letter-spacing: -0.01em;
  }
</style>
</head>
<body>
  <main class="cover">
    <p class="cover__eyebrow">THE</p>
    <h1 class="cover__title">Plate<br>Compass</h1>

    <section class="cover__band">
      <svg width="811" height="590" viewBox="0 0 811 590" aria-label="Pyramid of nutrition priorities">
        <polygon points="405.5,28 127,555 684,555" fill="none" stroke="#ffffff" stroke-width="5"/>
        <g stroke="var(--rule)" stroke-width="1.3">
          <line x1="356" y1="139.5" x2="455" y2="139.5"/>
          <line x1="308" y1="233.5" x2="503" y2="233.5"/>
          <line x1="269" y1="332" x2="542" y2="332"/>
          <line x1="211" y1="434" x2="600" y2="434"/>
        </g>
        <g text-anchor="middle">
          <text class="pyramid__label" x="405.5" y="125" font-size="25">TIMING</text>
          <text class="pyramid__label" x="405.5" y="219" font-size="29">MICRONUTRIENTS</text>
          <text class="pyramid__label" x="405.5" y="317" font-size="33">MACRONUTRIENTS</text>
          <text class="pyramid__label" x="405.5" y="418" font-size="38">FOOD QUALITY</text>
          <text class="pyramid__label" x="405.5" y="524" font-size="41">CALORIES</text>
        </g>
      </svg>
    </section>

    <p class="cover__note">MOST IMPORTANT</p>
    <p class="cover__subtitle">Cutting Through the Noise<br>to What Actually Works</p>
    <p class="cover__author">AUTHOR NAME</p>
  </main>
</body>
</html>
```